Manifesto

I want a manifesto with the following five manifestos for our Not for Profit

- We are a For-purpose organisation
- Every service we offer is free
- Every product we sell funds our services
- Every financial transaction is transparent
- Our service is for the greater good
- Our purpose is always to serve the people
- We are a for purpose organisation

Its to go with this website logo/look/feel www.brightharbour.co.nz

Two attachments:

1. I quite like this look/feel of a manifesto (see attached), I want something clean, professional but I also quite like either Retro modern look feel also like a fresh, and uplifting as its for sick people coming to see us and our funds where anyone buys a product are used for helping those who are sick with healing......so needs something conveyed that is fresh, uplifing yet professional.
2. This attachment is how I wrote this down when inspired of how I wanted Bright Harbour to operate. This is our values chart. It has to say

Also check out our website for our logo, look etc.. it doesnt have to be the same but red somewhere would link back to logo. www.brightharbour.co.nz .

Industry/Entity Type

Financial

```html
<!DOCTYPE html>
<html lang="en">
<head>
<meta charset="utf-8">
<title>Bright Harbour Manifesto</title>
<link rel="stylesheet" href="https://fonts.googleapis.com/css2?family=Roboto+Slab:wght@700;800;900&family=Lobster&display=swap">
<style>
  :root {
    --backdrop: #e9e9e9;
    --poster-red: #93001a;
    --poster-edge: #5a0010;
    --ink-dark: #4b000f;
    --ink-light: #ffffff;
    --shadow: rgba(40, 0, 8, 0.9);
  }
  html, body {
    margin: 0;
    width: 1200px;
    height: 1000px;
    overflow: hidden;
    background: var(--backdrop);
  }
  .manifesto {
    position: absolute;
    left: 277px;
    top: 41px;
    width: 648px;
    height: 916px;
    background:
      radial-gradient(ellipse 75% 70% at 50% 50%, var(--poster-red) 60%, var(--poster-edge) 100%);
    overflow: hidden;
  }
  .line {
    position: absolute;
    left: 0;
    width: 648px;
    text-align: center;
    white-space: nowrap;
    line-height: 1;
    margin: 0;
  }
  .slab { font-family: "Roboto Slab", Georgia, serif; font-weight: 900; text-transform: uppercase; }
  .script { font-family: "Lobster", "Brush Script MT", cursive; font-weight: 400; }
  .dark { color: var(--ink-dark); }
  .light { color: var(--ink-light); text-shadow: 2px 3px 0 var(--shadow); }
  .split span { display: inline-block; vertical-align: top; }

  .intro { top: 26px; height: 80px; }
  .intro .we-are { position: absolute; left: 23px; top: 14px; font-size: 52px; }
  .intro .for-purpose { position: absolute; left: 318px; top: 0; font-size: 41px; font-weight: 800; }
  .intro .organisation { position: absolute; left: 318px; top: 44px; font-size: 37px; }

  .free { top: 126px; font-size: 50px; }
  .free .light { margin-right: 14px; }

  .product-head { top: 216px; font-size: 66px; font-weight: 800; }
  .product-tail { top: 281px; font-size: 40px; text-transform: lowercase; letter-spacing: 1px; }

  .finance-head { top: 352px; font-size: 42px; font-weight: 800; letter-spacing: 10px; text-indent: 10px; }
  .finance-tail { top: 398px; font-size: 28px; text-transform: lowercase; letter-spacing: 7.5px; text-indent: 7px; }

  .service-head { top: 472px; font-size: 60px; letter-spacing: 5px; }
  .service-tail { top: 536px; font-size: 50px; }

  .purpose-head { top: 620px; font-size: 60px; letter-spacing: 5px; }
  .purpose-tail { top: 680px; font-size: 47px; }

  .closing-head { top: 772px; font-size: 48px; letter-spacing: 1px; }
  .closing-tail { top: 818px; font-size: 74px; left: -20px; }
</style>
</head>
<body>
  <article class="manifesto" aria-label="Bright Harbour manifesto">
    <div class="line intro">
      <span class="slab dark we-are">We are a</span>
      <span class="slab light for-purpose">For purpose</span>
      <span class="slab dark organisation">Organisation</span>
    </div>

    <p class="line script free"><span class="light">EveryService</span><span class="dark">we offer is free</span></p>

    <p class="line slab light product-head">Every product</p>
    <p class="line slab dark product-tail">we sell funds our services</p>

    <p class="line slab light finance-head">Every financial</p>
    <p class="line slab dark finance-tail">transaction is transparent</p>

    <p class="line slab dark service-head">Our service is</p>
    <p class="line script light service-tail">for the greater good</p>

    <p class="line slab dark purpose-head">Our purpose is</p>
    <p class="line script light purpose-tail">always to serve the people</p>

    <p class="line slab dark closing-head">We are a for purpose</p>
    <p class="line script light closing-tail">organisation</p>
  </article>
</body>
</html>
```